4th Generation Family Business Needs a New Card Design!

We are a family owned 4th Generation company. We are based in the Sydney, Australia area and we are desperately in need of a more modern and classy card. We are monumental masons who design, supply & erect lasting memorials throughout cemeteries in Sydney. Our customers are normally in a period of grieving. I have attached logo files that will need to be implemented on the card. Company was established 1935. Australian Owned and Operated. Card needs to be designed to PIXO.com specification.

Target Market(s)

Our target market is based upon people that a grieving for family members that have passed away. We also deal with alot of companies that own and operate cemeteries.

Industry/Entity Type

Business

Contact Information for Business Card

Simon Harcourt, Operations Manager, 0417293086, simon@harcourtmemorials.com.au
Lewis Harcourt, Director, 0491630572, lewis@harcourtmemorials.com.au
Phone # 02 9561 3048
Website: www.harcourtmemorials.com.au
Address: Suite 17, 8 Palfrey Lane, West Carlow, Sydney NSW 2156

Font styles to use
Serif
Decorative
Script

Requirements
Must have
• Would like to see the logo nicely implemented with a modern design. Embossed lettering would be a nice additive.

```html
<!DOCTYPE html>
<html lang="en">
<head>
<meta charset="utf-8">
<title>Harcourt Memorials – Business Card</title>
<link rel="stylesheet" href="https://fonts.googleapis.com/css2?family=Arimo:wght@400;700&display=swap">
<style>
  :root {
    --backdrop: #e9e6e1;
    --card: #fbfbfa;
    --ink: #2b2b2b;
    --ink-soft: #6a6a6a;
    --gold: #e8c535;
    --rule: #3a3a3a;
  }
  * { margin: 0; padding: 0; box-sizing: border-box; }
  html, body {
    width: 1200px; height: 858px; overflow: hidden;
    background: var(--backdrop);
    font-family: "Arimo", Arial, sans-serif;
    color: var(--ink);
  }
  .canvas {
    width: 1200px; height: 858px;
    display: flex; align-items: center; justify-content: center; gap: 40px;
  }
  .card {
    width: 560px; height: 342px;
    background: var(--card);
    box-shadow: 0 2px 10px rgba(0,0,0,0.12);
    position: relative;
  }
  .wordmark {
    display: flex; align-items: center; gap: 12px;
    font-weight: 700; letter-spacing: 2px; color: var(--ink);
    text-transform: uppercase; line-height: 1.15;
  }
  .wordmark__square { width: 14px; height: 14px; background: var(--gold); flex: none; }

  /* contact side */
  .card--contact { display: flex; align-items: center; }
  .card--contact .brand-area {
    width: 230px; display: flex; justify-content: center; padding-left: 20px;
  }
  .card--contact .wordmark { font-size: 22px; }
  .divider { width: 1px; height: 190px; background: var(--rule); margin: 0 26px 0 10px; }
  .details { font-size: 12.5px; line-height: 1.45; }
  .details__names { font-size: 17px; margin-bottom: 2px; }
  .details__roles { font-size: 11px; color: var(--ink-soft); margin-bottom: 12px; }
  .details__block { margin-bottom: 10px; }

  /* logo side */
  .card--brand { display: flex; align-items: center; justify-content: center; }
  .card--brand .wordmark { font-size: 30px; letter-spacing: 3px; }
</style>
</head>
<body>
<main class="canvas">
  <section class="card card--contact">
    <div class="brand-area">
      <div class="wordmark">
        <span class="wordmark__square"></span>
        <span>Harcourt<br>Memorials</span>
      </div>
    </div>
    <div class="divider"></div>
    <div class="details">
      <p class="details__names">Simon Harcourt | Lewis Harcourt</p>
      <p class="details__roles">Operations Manager | Director</p>
      <div class="details__block">
        <p>0417293086 / 0491630572</p>
        <p>simon@harcourtmemorials.com.au</p>
        <p>lewis@harcourtmemorials.com.au</p>
      </div>
      <div class="details__block">
        <p>www.harcourtmemorials.com.au</p>
        <p>Suite 17, 8 Palfrey Lane, West Carlow,</p>
        <p>Sydney NSW 2156</p>
      </div>
    </div>
  </section>

  <section class="card card--brand">
    <div class="wordmark">
      <span class="wordmark__square"></span>
      <span>Harcourt<br>Memorials</span>
    </div>
  </section>
</main>
</body>
</html>
```